Church Website with Home Page and Member Sermon Library

I am in need of an updated design for our church website. This will include 4 pages (outlined below). We are a conservative, evangelical, Christian church. The site should be modern and clean, while still reflecting our conservative values. I already have a logo for our church, and I want the site to incorporate the logo, and match the logo/branding. Stock photos are allowed if needed, but I have uploaded some images of our church and would prefer those images to be used if possible. Any stock photos used should not include any people in the photos (scenery, nature, buildings, animals, etc. are fine).

The site will need 4 pages: Home, Support Us (Donate), Login, and Recording Library.

Page 1: Home
The home page should include the following sections:

- Navigation: Should include links to each section of the home page plus a "listen live" link which will take the user to a live-streaming site and a "support us" link which will take the user to a support/donate page.

- Announcements: Can be either a banner or some other design, but there needs to be some way for us to post announcements for visitors to see. I'm open for creative ideas in this section, but would like it not to take up a lot of room on the page.

- About Us: Should include address, service times (see attached document), and information about the church.

- Pastor Bio: A section that introduces our pastor and gives a short bio about our pastor. Would like this section to include a picture of our pastor. Somewhere in this section I would like to include this Bible reference: "And I will give you pastors according to mine heart, which shall feed you with knowledge and understanding. Jer 3:15 LPW"

- Articles of Faith (What We Believe): This should include several sub-sections each with a heading, body, and possibly 1 or more scripture references. I have attached a document to the brief that includes our articles of faith. Feel free to be creative with this section in how you lay these out and format them.

- Support Us: A small section that explains what kind of support someone can give and a link to a donation page. The link can say something like "Support Us" or "Donate Now".

- Contact form: A contact form that allows the visitor to send us a message. The contact form should ask for name, email, phone, and message.

- Footer: A footer that will be displayed on all pages of the site. This should include at a minimum a link to the home page (or a link to each individual section in the home page if you prefer), a link to "listen live", a link to "support us", a link to "contact us" (or you can put the contact form directly in the footer if you prefer), the address, and a "member login" link.

Page 2: Support Us
The donation page should include a form the visitor can fill out to make a donation. We will embed a third party form later. For this design, please just mock out the design with a basic form asking for name, phone, and email.

Page 3: Login
The recording library (detailed below) will require members to login with a shared numeric code before accessing the page. We need a design for a login screen. The screen should include navigation/footer just like all other pages, but the body of the login page will consist only of a form that asks the user to enter the access code and then a "login" button.

Page 4: Recording Library

The library page is a member-only page that will require a shared, numeric pass code to access. On this page, members will be able to access a filterable list of past sermons. The page by default should display most recent sermons, but should also include a search form that allows the member to filter the sermon list to find a particular sermon. The search form should allow the user to select a filter type (e.g. Speaker name, date, event, etc.) and type in a value to search. They should be able to add multiple filters and remove filters that have been added. Each sermon that is displayed in the result list should include basic information such as title, date, speaker, tags, etc. along with a download icon, and an embedded audio player where they can click a play button to stream it on-demand. Each sermon should also have clickable tags associated with it that can be used to find related sermons.
Updates

I have uploaded several images of our church. Feel free to incorporate these into your design if possible.

Target Market(s)

Church Members

Industry/Entity Type

Religion

Number of Pages Required

4 page

Font styles to use
Sans Serif

Colors

Designer to choose colors to be used in the design.

Requirements
Must have
• Must incorporate the logo (attached)
Nice to have
• Would like the design to incorporate pictures of our church (attached) instead of stock photos if possible.
Should not have
• Please avoid an overly cluttered design. Stock photos used should not include any people in the photos.

```html
<!DOCTYPE html>
<html lang="en">
<head>
<meta charset="utf-8">
<title>Donation – Cedar Hill Church</title>
<link href="https://fonts.googleapis.com/css2?family=Open+Sans:wght@300;400;600&family=Playfair+Display:wght@700&display=swap" rel="stylesheet">
<style>
:root{
  --ink:#2b2b2b;
  --green-dark:#426324;
  --green:#86ab6b;
  --teal:#15a9d0;
  --field:#f4f4f4;
  --footer:#363636;
  --white:#ffffff;
  --muted:#8a8a8a;
}
*{box-sizing:border-box;margin:0;padding:0}
html,body{width:825px;height:1200px;overflow:hidden}
body{position:relative;font-family:"Open Sans",sans-serif;color:var(--ink);background:var(--white)}
.abs{position:absolute}
.site-header{left:0;top:0;width:825px;height:56px;background:var(--white)}
.brand{left:98px;top:18px;display:flex;align-items:center;gap:5px;font-size:11px;font-weight:600;color:var(--green-dark);letter-spacing:.5px}
.brand-mark{width:9px;height:9px;border-radius:50%;background:var(--teal)}
.main-nav a{position:absolute;top:23px;font-size:7.6px;color:var(--ink);text-decoration:none;letter-spacing:.3px}
.pill{display:flex;align-items:center;gap:4px;height:23px;border-radius:2px;color:var(--white);font-size:7.6px;line-height:8px;padding:0 4px;text-decoration:none}
.pill.listen{background:var(--green)}
.pill.support{background:var(--teal)}
.pill svg{flex:none}
.hero{left:0;top:56px;width:825px;height:171px;background:linear-gradient(100deg,#5e4a3c 0%,#7b6250 45%,#8d8378 70%,#6e6a66 100%)}
.hero-rule{left:107px;top:147px;width:53px;height:1px;background:var(--white)}
.hero-title{left:171px;top:132px;font-family:"Playfair Display",serif;font-size:23px;color:var(--white)}
.crumbs{left:107px;top:200px;font-size:10.5px;color:var(--white)}
.crumbs span{margin:0 9px}
.donation-card{left:120px;top:273px;width:583px;height:587px;background:var(--white);box-shadow:0 0 10px rgba(0,0,0,.08)}
.card-head{left:0;top:0;width:583px;height:129px;background:var(--green-dark)}
.head-graphic{left:29px;top:14px;width:93px;height:101px;border-radius:50%;background:rgba(255,255,255,.85)}
.card-title{left:140px;top:44px;font-family:"Playfair Display",serif;font-size:29px;color:var(--white)}
.label{font-size:9.6px;color:var(--ink)}
.field{background:var(--field);height:28px;font-size:8.6px;font-weight:300;color:#555;display:flex;align-items:center;padding-left:8px}
.hint{font-size:5.3px;color:var(--muted)}
.donate-btn{left:221px;top:528px;width:132px;height:36px;background:var(--green);color:var(--white);font-size:15.5px;display:flex;align-items:center;justify-content:center;border-radius:2px}
.site-footer{left:0;top:909px;width:825px;height:291px;background:var(--footer)}
.footer-brand{left:0;width:825px;top:110px;display:flex;justify-content:center;align-items:center;gap:6px;font-size:15px;font-weight:600;color:var(--green)}
.footer-nav{left:0;width:825px;top:180px;display:flex;justify-content:center;gap:0;font-size:7.6px;font-weight:600;color:var(--white)}
.footer-nav span{padding:0 9px;border-right:1px solid var(--green)}
.footer-nav span:last-child{border-right:none}
.footer-pills{left:356px;top:210px;display:flex;gap:8px}
.copyright{left:0;width:825px;top:269px;text-align:center;font-size:7.6px;font-weight:300;color:#bbb}
</style>
</head>
<body>
<header class="site-header abs">
  <div class="brand abs"><span class="brand-mark"></span>Cedar Hill Church</div>
  <nav class="main-nav">
    <a style="left:250px">HOME</a>
    <a style="left:293px">ANNOUNCEMENTS</a>
    <a style="left:384px">ABOUT US</a>
    <a style="left:446px">PASTOR BIO</a>
    <a style="left:514px">ARTICLES OF FAITH</a>
  </nav>
  <a class="pill listen abs" style="left:600px;top:18px">
    <svg width="14" height="14" viewBox="0 0 14 14" fill="none" stroke="#fff" stroke-width="1.3"><path d="M2 9V7a5 5 0 0 1 10 0v2"/><rect x="1.5" y="8.5" width="2.5" height="4" rx=".8"/><rect x="10" y="8.5" width="2.5" height="4" rx=".8"/></svg>listen<br>live</a>
  <a class="pill support abs" style="left:657px;top:18px">
    <svg width="16" height="14" viewBox="0 0 16 14" fill="none" stroke="#fff" stroke-width="1.2"><path d="M8 13 2 7a3.3 3.3 0 0 1 6-4 3.3 3.3 0 0 1 6 4z"/></svg>Support<br>Us</a>
</header>

<section class="hero abs" role="img" aria-label="Photo of the brick church building with its sign board"></section>
<div class="hero-rule abs"></div>
<h1 class="hero-title abs">Donation</h1>
<div class="crumbs abs">Home<span>›</span>Donation</div>

<main class="donation-card abs">
  <div class="card-head abs">
    <div class="head-graphic abs" role="img" aria-label="Emblem of four joined hands"></div>
    <h2 class="card-title abs">Donation Form</h2>
  </div>
  <div class="label abs" style="left:15px;top:155px">Full Name</div>
  <div class="field abs" style="left:15px;top:172px;width:270px"></div>
  <div class="field abs" style="left:296px;top:172px;width:272px"></div>
  <div class="hint abs" style="left:17px;top:203px">First Name</div>
  <div class="hint abs" style="left:298px;top:203px">Last Name</div>

  <div class="label abs" style="left:15px;top:222px">Email</div>
  <div class="label abs" style="left:297px;top:222px">Phone</div>
  <div class="field abs" style="left:15px;top:240px;width:270px">ex: myname@example.com</div>
  <div class="field abs" style="left:296px;top:240px;width:272px"></div>

  <div class="label abs" style="left:15px;top:284px">Card Details:</div>
  <div class="field abs" style="left:15px;top:302px;width:270px">First Name</div>
  <div class="field abs" style="left:296px;top:302px;width:272px">Last Name</div>
  <div class="field abs" style="left:15px;top:347px;width:270px">
    <svg width="20" height="14" viewBox="0 0 20 14" style="margin-right:10px"><rect width="20" height="14" rx="1.5" fill="#222"/><rect y="3" width="20" height="2.5" fill="#f4f4f4"/><rect x="2" y="9" width="4" height="1.6" fill="#f4f4f4"/><rect x="7" y="9" width="3" height="1.6" fill="#f4f4f4"/></svg>Card Number</div>
  <div class="field abs" style="left:296px;top:347px;width:136px">MM/YY</div>
  <div class="field abs" style="left:443px;top:347px;width:124px">CVV</div>

  <div class="label abs" style="left:15px;top:393px">Comments</div>
  <div class="field abs" style="left:15px;top:411px;width:552px;height:90px"></div>

  <div class="donate-btn abs">Donate Now</div>
</main>

<footer class="site-footer abs">
  <div class="footer-brand abs"><span class="brand-mark"></span>Cedar Hill Church</div>
  <nav class="footer-nav abs">
    <span>HOME</span><span>ANNOUNCEMENTS</span><span>ABOUT US</span><span>PASTOR BIO</span><span>ARTICLES OF FAITH</span><span>CONTACT US</span>
  </nav>
  <div class="footer-pills abs">
    <a class="pill listen">
      <svg width="14" height="14" viewBox="0 0 14 14" fill="none" stroke="#fff" stroke-width="1.3"><path d="M2 9V7a5 5 0 0 1 10 0v2"/><rect x="1.5" y="8.5" width="2.5" height="4" rx=".8"/><rect x="10" y="8.5" width="2.5" height="4" rx=".8"/></svg>listen<br>live</a>
    <a class="pill support">
      <svg width="16" height="14" viewBox="0 0 16 14" fill="none" stroke="#fff" stroke-width="1.2"><path d="M8 13 2 7a3.3 3.3 0 0 1 6-4 3.3 3.3 0 0 1 6 4z"/></svg>Support<br>Us</a>
  </div>
  <p class="copyright abs">© 2023 Cedar Hill Church. All rights reserved. Privacy Policy</p>
</footer>
</body>
</html>
```